Business card for Eyelash extension salon in Beverly Hills,California USA

We need new business card for our salon in Beverly Hills. The salon name is 'Lashvera' . We would like to have...Business name: Lashvera Name of person: will provide later Address 4720 N.Alder Crest Ave Cedar Hollow , CA 90417 Phone: will provide later (Text only) Web: www.lashverastudio.example Snapgrid icon, Circlebook icon follow us for seasonal campaign and news @lashverastudiolounge Design should look elegant, high-end, clean, simple, cohesive with my brand. Please refer my brand board. Business name color will be metallic bronzy color. Im thinking grey background or white background. Thanks

Target Market(s)

25-35. Gender neutral. People who are in Entertainment business industry.
This is High-end Eyelash extension salon in Beverly Hills

Industry/Entity Type

Beauty Salon

Contact Information for Business Card

Business name: Lashvera
Name of person: will provide later
Address 4720 N.Alder Crest Ave Cedar Hollow , CA 90417
Phone: will provide later (Text only)
Web: www.lashverastudio.example
Snapgrid icon, Circlebook icon
follow us for seasonal campaign and news @lashverastudiolounge

Requirements
Must have
• Beautiful, elegant, clean and simple look but very attractive and modern
Should not have
• We don't like too clutter, too busy designs.

```html
<!DOCTYPE html>
<html lang="en">
<head>
<meta charset="utf-8">
<title>Lashvera Business Card</title>
<link rel="stylesheet" href="https://fonts.googleapis.com/css2?family=Mulish:wght@400;800&display=swap">
<style>
  :root {
    --page-bg: #ffffff;
    --card-grey: #b5b4b9;
    --ink: #111111;
    --bronze: #b8892a;
    --gold-dark: #9a6f16;
    --gold-mid: #d4ae3a;
    --gold-light: #f3e39a;
  }
  html, body {
    margin: 0;
    padding: 0;
    width: 1200px;
    height: 900px;
    overflow: hidden;
    background: var(--page-bg);
    font-family: "Mulish", Arial, sans-serif;
  }
  .canvas {
    position: relative;
    width: 1200px;
    height: 900px;
  }
  .card {
    position: absolute;
    left: 333px;
    width: 532px;
    height: 295px;
    background: var(--card-grey);
    overflow: hidden;
  }
  .card--front { top: 113px; }
  .card--back { top: 477px; }

  .brand-name {
    position: absolute;
    margin: 0;
    color: var(--bronze);
    font-weight: 400;
    letter-spacing: 1px;
    white-space: nowrap;
  }
  .card--front .brand-name {
    left: 12px;
    top: 126px;
    width: 200px;
    text-align: center;
    font-size: 36px;
  }
  .divider {
    position: absolute;
    left: 219px;
    top: 37px;
    width: 2px;
    height: 221px;
    background: var(--ink);
  }
  .contact {
    position: absolute;
    left: 226px;
    top: 38px;
    color: var(--ink);
  }
  .person {
    margin: 0 0 4px 32px;
    font-weight: 800;
    font-size: 14.5px;
    line-height: 17px;
  }
  .contact-list {
    list-style: none;
    margin: 0;
    padding: 0;
  }
  .contact-list li {
    display: flex;
    align-items: flex-start;
    font-size: 18.5px;
    line-height: 26.6px;
    letter-spacing: 0;
    white-space: nowrap;
  }
  .contact-list .icon {
    width: 16px;
    height: 16px;
    margin: 5px 12px 0 4px;
    flex: none;
  }
  .contact-list .icon--none { visibility: hidden; }

  .foil-stripes {
    position: absolute;
    left: 0;
    top: 0;
    width: 268px;
    height: 295px;
    background: linear-gradient(90deg, var(--gold-dark), var(--gold-mid) 35%, var(--gold-light) 60%, var(--gold-mid) 85%, var(--card-grey));
  }
  .card--back .brand-name {
    left: 272px;
    top: 80px;
    width: 230px;
    text-align: center;
    font-size: 52px;
  }
  .brand-rule {
    position: absolute;
    left: 278px;
    top: 185px;
    width: 224px;
    height: 3px;
    background: linear-gradient(90deg, var(--gold-dark), var(--gold-mid), var(--gold-dark));
  }
</style>
</head>
<body>
<main class="canvas">

  <section class="card card--front" aria-label="Business card front">
    <p class="brand-name">Lashvera</p>
    <div class="divider"></div>
    <div class="contact">
      <p class="person">Your Name<br>Your Position</p>
      <ul class="contact-list">
        <li>
          <svg class="icon" viewBox="0 0 16 16" aria-hidden="true"><circle cx="8" cy="8" r="7.2" fill="none" stroke="#111" stroke-width="1.3"/><path d="M8 3.4a3 3 0 0 0-3 3c0 2.2 3 5.8 3 5.8s3-3.6 3-5.8a3 3 0 0 0-3-3z" fill="#111"/><circle cx="8" cy="6.4" r="1.1" fill="#b5b4b9"/></svg>
          <span>4720 N.Alder Crest Ave</span>
        </li>
        <li>
          <span class="icon icon--none"></span>
          <span>Cedar Hollow , CA 90417</span>
        </li>
        <li>
          <svg class="icon" viewBox="0 0 16 16" aria-hidden="true"><circle cx="8" cy="8" r="7.2" fill="none" stroke="#111" stroke-width="1.3"/><path d="M5.2 4.2l1.5-.3 1 2-.9.8c.4 1 1.2 1.8 2.2 2.2l.8-.9 2 1-.3 1.5c-3 .4-6.6-3.2-6.3-6.3z" fill="#111"/></svg>
          <span>+1 310 - 555- 0142</span>
        </li>
        <li>
          <svg class="icon" viewBox="0 0 16 16" aria-hidden="true"><circle cx="8" cy="8" r="7.2" fill="none" stroke="#111" stroke-width="1.3"/><circle cx="8" cy="8" r="4.2" fill="#111"/><path d="M4 8h8M8 3.8c-1.5 2.6-1.5 5.8 0 8.4M8 3.8c1.5 2.6 1.5 5.8 0 8.4" stroke="#b5b4b9" stroke-width="0.8" fill="none"/></svg>
          <span>www.lashverastudio.example</span>
        </li>
        <li>
          <svg class="icon" viewBox="0 0 16 16" aria-hidden="true"><circle cx="8" cy="8" r="7.2" fill="none" stroke="#111" stroke-width="1.3"/><circle cx="8" cy="8" r="3.6" fill="#111"/></svg>
          <span>Follow us on Snapgrid</span>
        </li>
        <li>
          <svg class="icon" viewBox="0 0 16 16" aria-hidden="true"><circle cx="8" cy="8" r="7.2" fill="none" stroke="#111" stroke-width="1.3"/><circle cx="8" cy="8" r="3.6" fill="#111"/></svg>
          <span>Follow us on Circlebook</span>
        </li>
        <li>
          <svg class="icon" viewBox="0 0 16 16" aria-hidden="true"><circle cx="8" cy="8" r="7.2" fill="#111"/><rect x="4" y="5.2" width="8" height="5.6" fill="none" stroke="#b5b4b9" stroke-width="0.9"/><path d="M4 5.4l4 3 4-3" fill="none" stroke="#b5b4b9" stroke-width="0.9"/></svg>
          <span>Follow us on Email</span>
        </li>
      </ul>
    </div>
  </section>

  <section class="card card--back" aria-label="Business card back">
    <div class="foil-stripes" role="img" aria-label="Gold foil decorative stripe area"></div>
    <p class="brand-name">Lashvera</p>
    <div class="brand-rule"></div>
  </section>

</main>
</body>
</html>
```